WP website design (Harrowgate)

We need a wordpress design for an established auction and real estate company based in Florida. The winning design will incorporate a professional color scheme with company logo in a clean layout. The design needs to consider that this will be developed on a responsive theme. Colors are those that will highlight the logo.

Industry/Entity Type

Real Estate

Font styles to use
Serif
Sans Serif

Colors

Designer to choose colors to be used in the design.

Requirements
Must have
• Navigation:
1) Home
2) Auctions
3) Online Auctions
4) About Us
5) Services
6) Real Estate Listings
7) References
8) Contact Us

Colors will be blue (#000066) / red (#B10000) and black or other complementary color. Tagline to be used "Since 1977, Proven Results." Slideshow to be placed in the header or body of home page - please use stock real estate image.

Widgets: 1) Email Sign-up 2) Social media icons for FB and LinkedIn 3) Featured Listings 4) Testimonials 5) Register button

Footer will have smaller company logo, attached logos and contact info:
Phone: (555) 261-0948 Mobile: (555) 718-3062
Email: mirelharrowgate@quellmail.example
Address: 58 E. Tamsin Avenue, Ste 410, Pensacola, FL 32599
Nice to have
• Use of a drop down menu:
Auctions-
1) Upcoming Auctions
2) Past Auctions

```html
<!DOCTYPE html>
<html lang="en">
<head>
<meta charset="utf-8">
<title>Harrowgate Auctions</title>
<link href="https://fonts.googleapis.com/css2?family=Arimo:wght@400;700&family=Crimson+Text:wght@400;600;700&display=swap" rel="stylesheet">
<style>
:root{
  --red:#b10000;
  --red-dark:#8e0000;
  --navy:#000066;
  --ink:#222;
  --muted:#555;
  --panel:#c9c9c9;
  --field:#fff;
  --footer:#cfcfcf;
  --line:#d9d9d9;
}
*{box-sizing:border-box;margin:0;padding:0}
html,body{width:1200px;height:2826px;overflow:hidden}
body{position:relative;background:#fff;font-family:"Arimo",Arial,sans-serif;color:var(--ink)}
.abs{position:absolute}
.serif{font-family:"Crimson Text",Georgia,serif}

.topbar{left:0;top:0;width:1200px;height:38px;background:var(--red);color:#fff;font-size:13px}
.topbar .item{position:absolute;top:11px;display:flex;align-items:center;gap:8px}
.header{left:0;top:38px;width:1200px;height:90px;background:#fff}
.brand{left:132px;top:47px;display:flex;align-items:center;gap:14px}
.brand .mark{width:62px;height:62px;background:var(--navy)}
.brand .name{font-size:40px;font-weight:700;color:var(--navy);line-height:1}
.btn{background:var(--red);color:#fff;font-size:14px;display:flex;align-items:center;justify-content:center;gap:10px;border-radius:3px}
.register{left:899px;top:70px;width:162px;height:31px;font-size:13px}
.rule{left:0;width:1200px;height:6px;background:var(--red)}
.nav{left:0;top:134px;width:1200px;height:45px;background:#fff}
.nav a{position:absolute;top:15px;font-size:14px;color:var(--navy);text-decoration:none}
.nav a.active{color:var(--red)}
.dropdown{left:220px;top:185px;width:149px;height:92px;background:var(--red);z-index:3;padding-top:12px}
.dropdown a{display:block;color:#fff;font-size:13px;padding:9px 0 10px 12px;text-decoration:none}

.hero{left:0;top:185px;width:1200px;height:427px;background:linear-gradient(180deg,#6f8a5c 0%,#c9c7bd 40%,#d8d6cc 70%,#5f6f45 100%)}
.tagline{left:132px;top:392px;width:397px;height:166px;background:rgba(0,0,0,.82);color:#fff;font-size:45px;font-weight:700;line-height:68px;padding:14px 0 0 20px;white-space:nowrap}
.hero-arrow{top:385px}

h2.section{position:absolute;color:var(--red);font-size:29px;font-weight:700}
.welcome-photo{left:132px;top:722px;width:254px;height:254px;border-radius:50%;border:4px solid var(--red);background:radial-gradient(circle at 50% 40%,#eee 0%,#d9d9d9 55%,#bdbdbd 100%)}
.welcome-text{left:411px;top:711px;width:660px;font-size:13px;line-height:45px;color:#333;white-space:nowrap}
.readmore{left:413px;top:919px;width:149px;height:38px}

.service{top:1093px;width:296px;height:192px;background:linear-gradient(160deg,#8a7a66,#c9c2b7)}
.service.s2{background:linear-gradient(160deg,#3fa4ad,#a8d6d9)}
.service.s3{background:linear-gradient(160deg,#b8b8b0,#e6e6e0)}
.service .cap{position:absolute;left:0;bottom:0;width:100%;height:40px;background:rgba(0,0,0,.78);color:#fff;font-size:17px;text-align:center;line-height:40px}
.service .cap.open{height:115px;text-align:left;line-height:1.5;padding:14px 12px 0 12px;font-size:16px}
.service .cap.open p{font-size:12.5px;font-weight:700;margin-top:6px}

.browse{left:132px;top:1338px;width:269px;height:599px;background:var(--panel)}
.browse .head{height:41px;background:var(--red);color:#fff;font-size:23px;display:flex;align-items:center;gap:12px;padding-left:28px}
.field-label{position:absolute;left:27px;font-size:14px;color:#333}
.select{position:absolute;left:25px;width:221px;height:33px;background:var(--field);border:1px solid #bbb;font-size:13px;color:#333;padding:9px 0 0 9px}
.select:after{content:"";position:absolute;right:0;top:0;width:20px;height:31px;border-left:1px solid #ddd;background:#f2f2f2}
.select svg{position:absolute;right:6px;top:13px;z-index:1}
.search{left:66px;top:534px;width:140px;height:31px;font-size:13px}

.listing-photo{left:448px;width:283px;height:162px;background:linear-gradient(180deg,#8fb5dc 0%,#b9cce0 35%,#a9765c 60%,#6f7d4e 100%)}
.listing-photo.l2{background:linear-gradient(180deg,#6d97cf 0%,#b6cde6 35%,#e8e8e4 60%,#54663a 100%)}
.listing-photo.l3{background:linear-gradient(180deg,#7fa7d6 0%,#c2d2e3 35%,#9b8165 62%,#5d7343 100%)}
.price{left:774px;font-size:27px;font-weight:700;color:var(--red)}
.listing-desc{left:774px;font-size:14px;color:#555}
.specs{left:774px;width:292px;height:30px;background:var(--panel);font-size:14px;color:#333;padding:8px 0 0 12px}
.details{left:774px;width:143px;height:31px;font-size:13px}

.testimonials{left:132px;top:2046px;width:936px;height:245px;background:linear-gradient(90deg,#4a4a4a,#5d5752 50%,#4a4a4a)}
.person{position:absolute;top:18px;width:300px;text-align:center;color:#fff}
.person .avatar{width:126px;height:126px;border-radius:50%;border:4px solid #fff;margin:0 auto;background:linear-gradient(180deg,#9a9a9a,#6e6e6e)}
.person .name{font-size:14.5px;margin-top:14px}
.person .quote{font-size:14px;line-height:22px;margin-top:4px}

.certs{left:132px;top:2387px;width:936px;height:102px;border:1px solid var(--line);background:#fff}
.badge{position:absolute;top:22px;height:56px;background:#e6e6ea;border-radius:4px}

.footer{left:0;top:2536px;width:1200px;height:218px;background:var(--footer)}
.fcol{position:absolute;top:20px;font-size:14px;line-height:25px;color:#333}
.fcol h3{font-size:16px;font-weight:400;color:var(--red);margin-bottom:8px;display:flex;align-items:center;gap:8px}
.fcol h3 .sq{width:18px;height:18px;background:var(--navy)}
.contact-row{display:flex;align-items:center;gap:14px;margin-bottom:17px}
.mail-input{display:inline-block;width:158px;height:31px;background:#fff;border:1px solid #bbb;font-size:13px;padding:8px 0 0 9px;color:#555}
.send{display:inline-flex;width:104px;height:31px;font-size:13px;vertical-align:top;margin-left:8px}
.bottombar{left:0;top:2754px;width:1200px;height:72px;background:var(--red);color:#fff;font-size:12px}
.social{position:absolute;top:22px;width:30px;height:30px;border-radius:50%;background:#fff}
</style>
</head>
<body>

<div class="abs topbar">
  <div class="item" style="left:147px">
    <svg width="18" height="14" viewBox="0 0 18 14"><path d="M2 5c0-3 14-3 14 0l-3 1-1-2H6L5 6z" fill="#fff"/><rect x="4" y="7" width="10" height="6" rx="1" fill="#fff"/></svg>
    (555) 261-0948
  </div>
  <div class="item" style="left:274px">
    <svg width="18" height="13" viewBox="0 0 18 13"><rect width="18" height="13" fill="#fff"/><path d="M0 0l9 7 9-7" stroke="#b10000" stroke-width="1.5" fill="none"/></svg>
    mirelharrowgate@quellmail.example
  </div>
</div>

<div class="abs header"></div>
<div class="abs brand"><span class="mark"></span><span class="name">Harrowgate</span></div>
<div class="abs btn register">Register Now
  <svg width="16" height="16" viewBox="0 0 16 16"><circle cx="8" cy="8" r="8" fill="#fff"/><path d="M4 8h7M8 5l3 3-3 3" stroke="#b10000" stroke-width="2" fill="none"/></svg>
</div>

<div class="abs rule" style="top:128px"></div>
<nav class="abs nav">
  <a style="left:136px">Home</a>
  <a class="active" style="left:224px">Auctions</a>
  <a style="left:330px">Online Auctions</a>
  <a style="left:479px">About Us</a>
  <a style="left:586px">Services</a>
  <a style="left:691px">Real Estate Listings</a>
  <a style="left:867px">References</a>
  <a style="left:989px">Contact Us</a>
</nav>
<div class="abs rule" style="top:179px"></div>

<div class="abs hero" role="img" aria-label="Slideshow photo of a pale suburban house with dormers, garage and green lawn"></div>
<svg class="abs hero-arrow" style="left:66px" width="16" height="28" viewBox="0 0 16 28"><path d="M14 2L3 14l11 12" stroke="#fff" stroke-width="3" fill="none"/></svg>
<svg class="abs hero-arrow" style="left:1100px" width="16" height="28" viewBox="0 0 16 28"><path d="M2 2l11 12L2 26" stroke="#fff" stroke-width="3" fill="none"/></svg>
<div class="abs tagline">Since 1977,<br>Proven Results.</div>

<div class="abs dropdown">
  <a>Upcoming Auctions</a>
  <a>Past Auctions</a>
</div>

<h2 class="section serif" style="left:132px;top:648px">Welcome To Harrowgate Auctions</h2>
<div class="abs welcome-photo" role="img" aria-label="Portrait of a smiling agent in a suit offering a handshake"></div>
<p class="abs welcome-text">Dummy text is also used to demonstrate the appearance of different typefaces and layouts, and in gen-<br>eral the content of dummy text is nonsensical. Due to its widespread use as filler text for layouts, non-<br>readability is of great importance: human perception is tuned to recognize certain patterns and repeti-<br>tions in texts.Due to its widespread use as filler text for layouts, non-readability is of great.</p>
<div class="abs btn readmore">Read More...</div>

<h2 class="section serif" style="left:132px;top:1022px">Our Services</h2>
<div class="abs service" style="left:132px" role="img" aria-label="Warm lit interior with kitchen and dining area">
  <div class="cap open">Leorem Ipsum<p>Lorem ipsum dolor sit amet, consectetuer adipiscing elit. Aenean commodo ligula eget dolor.</p></div>
</div>
<div class="abs service s2" style="left:452px" role="img" aria-label="Bright teal living room interior">
  <div class="cap">Leorem Ipsum</div>
</div>
<div class="abs service s3" style="left:771px" role="img" aria-label="Modern hallway with a staircase">
  <div class="cap">Leorem Ipsum</div>
</div>

<aside class="abs browse">
  <div class="head serif">
    <svg width="17" height="17" viewBox="0 0 17 17"><circle cx="7" cy="7" r="5" stroke="#fff" stroke-width="2.5" fill="none"/><path d="M11 11l5 5" stroke="#fff" stroke-width="2.5"/></svg>
    Browse By...
  </div>
  <span class="field-label" style="top:74px">Location</span>
  <div class="select" style="top:104px">Anywhere<svg width="8" height="5"><path d="M0 0h8L4 5z" fill="#888"/></svg></div>
  <span class="field-label" style="top:166px">Rent or Buy</span>
  <div class="select" style="top:195px">Any<svg width="8" height="5"><path d="M0 0h8L4 5z" fill="#888"/></svg></div>
  <span class="field-label" style="top:259px">Bedrooms</span>
  <div class="select" style="top:288px">Any<svg width="8" height="5"><path d="M0 0h8L4 5z" fill="#888"/></svg></div>
  <span class="field-label" style="top:352px">Bathrooms</span>
  <div class="select" style="top:380px">Any<svg width="8" height="5"><path d="M0 0h8L4 5z" fill="#888"/></svg></div>
  <span class="field-label" style="top:449px">Max Price</span>
  <div class="select" style="top:477px">Any<svg width="8" height="5"><path d="M0 0h8L4 5z" fill="#888"/></svg></div>
  <div class="abs btn search">Search</div>
</aside>

<h2 class="section serif" style="left:447px;top:1324px">Featured Listings</h2>

<div class="abs listing-photo" style="top:1390px" role="img" aria-label="Cream house with red roof and porch"></div>
<div class="abs price serif" style="top:1380px">$1,200,000</div>
<div class="abs listing-desc" style="top:1428px">Lorem ipsum dolor sit amet</div>
<div class="abs specs" style="top:1469px">4 Bedrooms , 3 Bathrooms</div>
<div class="abs btn details" style="top:1518px">More Details...</div>

<div class="abs listing-photo l2" style="top:1583px" role="img" aria-label="White modern two-storey house with dark roof"></div>
<div class="abs price serif" style="top:1572px">$1,200,000</div>
<div class="abs listing-desc" style="top:1620px">Lorem ipsum dolor sit amet</div>
<div class="abs specs" style="top:1661px">4 Bedrooms , 3 Bathrooms</div>
<div class="abs btn details" style="top:1710px">More Details...</div>

<div class="abs listing-photo l3" style="top:1775px" role="img" aria-label="Stone family house with double garage"></div>
<div class="abs price serif" style="top:1764px">$1,200,000</div>
<div class="abs listing-desc" style="top:1812px">Lorem ipsum dolor sit amet</div>
<div class="abs specs" style="top:1853px">4 Bedrooms , 3 Bathrooms</div>
<div class="abs btn details" style="top:1902px">More Details...</div>

<h2 class="section serif" style="left:132px;top:1976px">Testimonials</h2>
<section class="abs testimonials" role="img" aria-label="Dimmed interior backdrop behind client testimonials">
  <div class="person" style="left:-1px">
    <div class="avatar" role="img" aria-label="Client portrait"></div>
    <div class="name">SARAH</div>
    <div class="quote">Lorem ipsum dolor amet, consec-<br>tetur adipiscing elit.</div>
  </div>
  <div class="person" style="left:319px">
    <div class="avatar" role="img" aria-label="Client portrait"></div>
    <div class="name">JOHN</div>
    <div class="quote">Lorem ipsum dolor amet, consec-<br>tetur adipiscing elit.</div>
  </div>
  <div class="person" style="left:634px">
    <div class="avatar" role="img" aria-label="Client portrait"></div>
    <div class="name">STEVE</div>
    <div class="quote">Lorem ipsum dolor amet, consec-<br>tetur adipiscing elit.</div>
  </div>
</section>

<h2 class="section serif" style="left:132px;top:2328px">Certifications</h2>
<div class="abs certs">
  <div class="badge" style="left:12px;width:206px"></div>
  <div class="badge" style="left:236px;width:102px"></div>
  <div class="badge" style="left:360px;width:60px"></div>
  <div class="badge" style="left:442px;width:128px"></div>
  <div class="badge" style="left:592px;width:264px"></div>
  <svg class="abs" style="left:910px;top:40px" width="12" height="22" viewBox="0 0 12 22"><path d="M2 2l8 9-8 9" stroke="#999" stroke-width="2" fill="none"/></svg>
</div>

<footer class="abs footer">
  <div class="fcol" style="left:166px;width:250px">
    <h3><span class="sq"></span>Harrowgate Auctions</h3>
    Lorem ipsum dolor amet, consectetur adipiscing elit. Sed ut purus eget nunc ut dignissim cursus at a nisl. Mauris vitae turpis quis eros egestas tempor sit amet a arcu.
  </div>
  <div class="fcol" style="left:481px;width:260px">
    <h3>Contact Us</h3>
    <div class="contact-row">
      <svg width="14" height="20" viewBox="0 0 14 20"><path d="M7 0a7 7 0 017 7c0 5-7 13-7 13S0 12 0 7a7 7 0 017-7z" fill="#444"/><circle cx="7" cy="7" r="2.6" fill="#cfcfcf"/></svg>
      <span>58 E. Tamsin Avenue, Ste 410,<br>Pensacola, FL 32599</span>
    </div>
    <div class="contact-row">
      <svg width="20" height="16" viewBox="0 0 20 16"><path d="M1 6c0-5 18-5 18 0l-4 1-1-3H6L5 7z" fill="#444"/><rect x="4" y="8" width="12" height="8" rx="1" fill="#444"/></svg>
      <span>(555) 261-0948</span>
    </div>
    <div class="contact-row">
      <svg width="14" height="22" viewBox="0 0 14 22"><rect x="1" y="1" width="12" height="20" rx="2" stroke="#444" stroke-width="2" fill="none"/><circle cx="7" cy="17" r="1.3" fill="#444"/></svg>
      <span>(555) 718-3062</span>
    </div>
  </div>
  <div class="fcol" style="left:761px;width:300px">
    <h3>NewsLetter</h3>
    Lorem ipsum dolor amet, consectetur adipiscing elit. Sed ut purus eget nunc ut dignissim cursus at a nisl.
    <div style="margin-top:14px"><span class="mail-input">Your Mail</span><span class="btn send">SEND</span></div>
  </div>
</footer>

<div class="abs bottombar">
  <span class="abs" style="left:170px;top:29px">© 2014 Harrowgate Auctions, All Rights Reserved.</span>
  <span class="social" style="left:972px"></span>
  <span class="social" style="left:1012px"></span>
</div>

</body>
</html>
```